New Business Card Design Project

I need a design for business cards, i am an electrical business called "Corvane Electrical and Communications" i need the cards to be double sided with the company logo on the back (attached) the front needs to say my company name, web site, email address, telephone number, and ABN number and electrical license number. I am open to different arrangements of the information but would like the background to be incorporating something electrical or something that looks smart. open to all additional ideas also.

The company colours are orange and grey see logo attached.

Business Name: Corvane Electrical and Communications
Website: corvaneelectricalandcomms.example.com.au
Email: brent@corvaneelectricalandcomms.example.com.au
Telephone(mobile): 0481209736
ABN: 71208349162
Lic No: 418273D

Target Market(s)

Business entities, Project Managers, Accounts, Clients

Industry/Entity Type

Electrician

Contact Information for Business Card

I need a design for business cards, i am an electrical business called "Corvane Electrical and Communications" i need the cards to be double sided with the company logo on the back (attached) the front needs to say my company name

Font styles to use
Serif
Sans Serif

Colors
f37122
5c5c5c

Requirements
Must have
• Must have the Logo on the back open to different ways of it being on the back but had in mind to keep it central but again open to other options
Nice to have
• A real modern cool background that is eye catching yet contemporary
Should not have
• No backgrounds of a light bulb or plug or anything like that

```html
<!DOCTYPE html>
<html lang="en">
<head>
<meta charset="utf-8">
<title>Corvane Electrical and Communications – Business Cards</title>
<link rel="stylesheet" href="https://fonts.googleapis.com/css2?family=Ubuntu:wght@400;500&display=swap">
<style>
  :root {
    --page-bg: #e9e7e3;
    --card-grey: #5c5c5c;
    --card-grey-dark: #4a4a4a;
    --brand-orange: #f37122;
    --text-white: #f4f4f4;
    --text-soft: #d9d9d9;
    --card-shadow: rgba(0, 0, 0, 0.28);
  }
  * { box-sizing: border-box; margin: 0; padding: 0; }
  html, body {
    width: 1200px;
    height: 780px;
    overflow: hidden;
    background: var(--page-bg);
    font-family: "Ubuntu", "Helvetica Neue", Arial, sans-serif;
  }
  .canvas {
    position: relative;
    width: 1200px;
    height: 780px;
    display: flex;
    align-items: center;
    justify-content: center;
    gap: 60px;
  }
  .card {
    position: relative;
    width: 525px;
    height: 300px;
    border-radius: 4px;
    background: radial-gradient(ellipse at 60% 40%, var(--card-grey) 0%, var(--card-grey-dark) 100%);
    box-shadow: 0 6px 18px var(--card-shadow);
    overflow: hidden;
  }

  /* Front side: contact details */
  .card-front { padding: 40px 0 0 58px; }
  .person-name {
    color: var(--text-white);
    font-size: 27px;
    font-weight: 400;
    letter-spacing: 0.2px;
  }
  .person-role {
    color: var(--brand-orange);
    font-size: 17px;
    margin-top: 2px;
  }
  .contact-list {
    list-style: none;
    margin-top: 26px;
    font-size: 14.5px;
    line-height: 1.55;
    color: var(--text-white);
  }
  .contact-label { color: var(--brand-orange); }
  .contact-divider { color: var(--text-soft); padding: 0 4px; }
  .company-name {
    margin-top: 22px;
    color: var(--text-white);
    font-size: 14.5px;
    font-weight: 500;
  }
  .website {
    margin-top: 4px;
    color: var(--brand-orange);
    font-size: 15px;
  }

  /* Back side: company name */
  .card-back {
    display: flex;
    align-items: center;
    justify-content: center;
    gap: 18px;
  }
  .brand-dot {
    width: 22px;
    height: 22px;
    border-radius: 50%;
    background: var(--brand-orange);
    flex: none;
  }
  .brand-name {
    color: var(--text-white);
    font-size: 26px;
    font-weight: 500;
    line-height: 1.25;
  }
</style>
</head>
<body>
  <main class="canvas">
    <section class="card card-front" aria-label="Business card front">
      <h1 class="person-name">Employee Name</h1>
      <p class="person-role">Principal</p>
      <ul class="contact-list">
        <li><span class="contact-label">M:</span> 0481209736</li>
        <li><span class="contact-label">E:</span> brent@corvaneelectricalandcomms.example.com.au</li>
        <li><span class="contact-label">ABN:</span> 71208349162<span class="contact-divider">|</span><span class="contact-label">Lic No:</span> 418273D</li>
      </ul>
      <p class="company-name">Corvane Electrical and Communications</p>
      <p class="website">corvaneelectricalandcomms.example.com.au</p>
    </section>

    <section class="card card-back" aria-label="Business card back">
      <span class="brand-dot"></span>
      <p class="brand-name">Corvane Electrical<br>and Communications</p>
    </section>
  </main>
</body>
</html>
```